Valdane Companies Business Card Design

We need a new business card for our Private Equity Real Estate Development firm, “Valdane” and our EB-5 regional center “Thornmere Regional Center” on one card. We prefer a design that is simple, elegant, and represents the luxury products we design and build as well as the financial security and stability our successful history has produced. We are an industry leader in our field and 3rd generation family business that has evolved into an institutional quality investment platform. Considered design size is standard business card dimensions (3.5 x 2 inches with an additional 1/8 inch space for design elements or backgrounds that extend beyond the finished size of your piece.

Target Market(s)

• High net worth individuals
• Highly skilled technical workers and physicians in the US seeking investment-based immigration opportunities
• Sophisticated private equity investors
• Intermediary partners include domestic attorneys and investment brokers, as well as international agent networks
• US real estate developers

Industry/Entity Type

Finance

Contact Information for Business Card

(Providing placeholder info for personal information, please design for longer character spaces, longer names and addresses etc..)
• Logo for Valdane
• Logo for Thornmere Regional Center
• Full name: Marcus Valdane
• Job title: CEO
• Email address: mvaldane@valdanecompanies.com
• Cell phone number: +1.555.314.2287
• Office number +1.555.628.4410
• Office address: Larkfield Court 5, 4817 Vista Orilla, Ashcombe, NV.
• Website: www.valdanecompanies.com

Font styles to use
Serif
Sans Serif

Colors
ec1f27
ffffff
000000

Requirements
Must have
• • Logo for Valdane
• • Logo for Thornmere Regional Center
• - Use rounded corners
• (See .ai file included for logos)
Nice to have
• • Simple, elegant design
• • Aesthetically compatible with our website design (www.valdanecompanies.com)
• • Color palette including but not limited to white, black, and red (as per logos)
Should not have
• - Not too much red color
• - Do not stack both logos on top of each other

```html
<!DOCTYPE html>
<html lang="en">
<head>
<meta charset="utf-8">
<title>Valdane Companies Business Card</title>
<link rel="stylesheet" href="https://fonts.googleapis.com/css2?family=Cinzel:wght@700&family=Crimson+Text:wght@400;600&display=swap">
<style>
  :root {
    --backdrop: #3a3a3c;
    --card: #ffffff;
    --ink: #1a1a1a;
    --charcoal: #3b3b3d;
    --crimson: #a51c30;
    --swoosh: #5a5a5c;
  }
  * { margin: 0; padding: 0; box-sizing: border-box; }
  html, body { width: 1200px; height: 1000px; overflow: hidden; }
  body {
    background: var(--backdrop);
    font-family: "Crimson Text", Georgia, serif;
    color: var(--ink);
    position: relative;
  }
  .card {
    position: absolute;
    left: 250px;
    width: 700px;
    height: 400px;
    background: var(--card);
    border-radius: 28px;
    overflow: hidden;
    box-shadow: 0 12px 30px rgba(0,0,0,0.35);
  }
  .card--front { top: 60px; }
  .card--back { top: 540px; }

  .brand {
    position: absolute;
    font-family: "Cinzel", "Times New Roman", serif;
    font-weight: 700;
    display: flex;
    align-items: center;
    gap: 14px;
  }
  .brand__mark { width: 18px; height: 18px; flex: none; }
  .brand--company { left: 70px; top: 128px; font-size: 46px; color: var(--charcoal); }
  .brand--company .brand__mark { background: var(--charcoal); }
  .divider {
    position: absolute;
    left: 372px; top: 90px;
    width: 2px; height: 150px;
    background: var(--crimson);
  }
  .contact { position: absolute; left: 396px; top: 96px; }
  .contact__name {
    font-family: "Cinzel", "Times New Roman", serif;
    font-weight: 700;
    font-size: 24px;
    color: var(--crimson);
    line-height: 1.1;
  }
  .contact__title { font-size: 16px; color: var(--ink); margin-bottom: 22px; }
  .contact__list { list-style: none; font-size: 17px; line-height: 1.5; }
  .contact__list li { display: flex; align-items: center; gap: 9px; }
  .contact__list svg { width: 13px; height: 13px; fill: var(--crimson); flex: none; }

  .band { position: absolute; left: 0; bottom: 0; width: 700px; height: 120px; }
  .band__url {
    position: absolute; right: 40px; bottom: 18px;
    color: #ffffff; font-size: 18px; font-weight: 600;
  }

  .brand--center {
    left: 70px; top: 80px;
    font-size: 34px; color: var(--crimson);
    line-height: 1.05;
  }
  .brand--center .brand__mark { background: var(--crimson); }
  .brand--center span { display: block; max-width: 330px; }
  .address {
    position: absolute; left: 70px; top: 272px;
    font-size: 19px; line-height: 1.35;
    display: flex; gap: 8px;
  }
  .address svg { width: 14px; height: 18px; fill: var(--crimson); margin-top: 3px; flex: none; }
</style>
</head>
<body>

<section class="card card--front" aria-label="Card front">
  <div class="brand brand--company"><i class="brand__mark"></i>Valdane</div>
  <div class="divider"></div>
  <div class="contact">
    <p class="contact__name">Marcus Valdane</p>
    <p class="contact__title">CEO</p>
    <ul class="contact__list">
      <li><svg viewBox="0 0 24 24"><path d="M6.6 10.8a15 15 0 0 0 6.6 6.6l2.2-2.2c.3-.3.7-.4 1-.2 1.1.4 2.3.6 3.6.6.6 0 1 .4 1 1V20c0 .6-.4 1-1 1C10.6 21 3 13.4 3 4c0-.6.4-1 1-1h3.5c.6 0 1 .4 1 1 0 1.3.2 2.5.6 3.6.1.3 0 .7-.2 1z"/></svg>+1.555.314.2287</li>
      <li><svg viewBox="0 0 24 24"><path d="M7 1h10a2 2 0 0 1 2 2v18a2 2 0 0 1-2 2H7a2 2 0 0 1-2-2V3a2 2 0 0 1 2-2zm0 4v13h10V5z"/></svg>+1.555.628.4410</li>
      <li><svg viewBox="0 0 24 24"><path d="M2 4h20v16H2zm2 2v.5l8 5.5 8-5.5V6z"/></svg>mvaldane@valdanecompanies.com</li>
    </ul>
  </div>
  <svg class="band" viewBox="0 0 700 120" preserveAspectRatio="none" aria-hidden="true">
    <path d="M0 4 C 160 30, 400 34, 700 40 L700 120 L0 120 Z" fill="var(--swoosh)"/>
    <path d="M0 12 C 170 38, 410 42, 700 50 L700 120 L0 120 Z" fill="#ffffff"/>
    <path d="M0 22 C 180 46, 420 54, 700 60 L700 120 L0 120 Z" fill="var(--crimson)"/>
  </svg>
  <span class="band__url">www.valdanecompanies.com</span>
</section>

<section class="card card--back" aria-label="Card back">
  <div class="brand brand--center"><i class="brand__mark"></i><span>Thornmere Regional Center</span></div>
  <p class="address">
    <svg viewBox="0 0 14 18"><path d="M7 0a7 7 0 0 0-7 7c0 5 7 11 7 11s7-6 7-11a7 7 0 0 0-7-7zm0 9.5A2.5 2.5 0 1 1 7 4.5a2.5 2.5 0 0 1 0 5z"/></svg>
    <span>Larkfield Court 5, 4817<br>Vista Orilla, Ashcombe, NV.</span>
  </p>
</section>

</body>
</html>
```